BrindleStaffing Business Card Design

We are a staffing company finding positions for dedicated nurses and physicians.

Target Market(s)

Business Professionals

Industry/Entity Type

Staffing

Contact Information for Business Card

Gordon Pratley
Chairman
417 39th Avenue South
SAINT PETERSBURG FL 33712
813-555-4172 Mobile
813-555-8036 Fax
gpratley@brindlestaffing.com
www.brindlestaffing.com

Font styles to use
Sans Serif

Colors
fbee3e
f04a50
f37122

Requirements
Must have
• Logo Attached, see colors below. We'd like to see Yellow, Orange and Red.

```html
<!DOCTYPE html>
<html lang="en">
<head>
<meta charset="utf-8">
<title>BrindleStaffing Business Card</title>
<link href="https://fonts.googleapis.com/css2?family=Roboto:wght@400;500;700&display=swap" rel="stylesheet">
<style>
  :root {
    --brand-yellow: #fbee3e;
    --brand-red: #f04a50;
    --brand-orange: #f37122;
    --text-grey: #555555;
    --card-white: #ffffff;
    --stage: #8a8a8a;
  }
  * { margin: 0; padding: 0; box-sizing: border-box; }
  html, body {
    width: 1125px;
    height: 1200px;
    overflow: hidden;
    background: var(--stage);
    font-family: "Roboto", Arial, sans-serif;
  }
  .card {
    position: absolute;
    left: 150px;
    width: 825px;
    height: 471px;
    overflow: hidden;
  }
  .card-front { top: 98px; background: var(--card-white); }
  .card-back { top: 631px; background: var(--brand-orange); }

  .wordmark {
    position: absolute;
    font-weight: 700;
    letter-spacing: -1px;
    white-space: nowrap;
  }
  .card-front .wordmark {
    left: 48px;
    top: 98px;
    font-size: 50px;
    color: var(--brand-orange);
  }
  .card-back .wordmark {
    left: 0;
    right: 0;
    top: 216px;
    text-align: center;
    font-size: 80px;
    color: var(--card-white);
  }

  .name-band {
    position: absolute;
    left: 438px;
    top: 197px;
    width: 387px;
    height: 97px;
  }
  .name-block {
    position: absolute;
    right: 61px;
    top: 208px;
    text-align: right;
    color: var(--card-white);
  }
  .name-block .person-name { font-size: 30px; font-weight: 700; line-height: 1.15; }
  .name-block .person-title { font-size: 20px; font-weight: 500; line-height: 1.2; }

  .address {
    position: absolute;
    left: 47px;
    top: 255px;
    font-size: 19px;
    line-height: 25px;
    color: var(--text-grey);
  }
  .contact-list {
    position: absolute;
    left: 50px;
    top: 317px;
    list-style: none;
    font-size: 19px;
    line-height: 26.8px;
    color: var(--text-grey);
  }
  .contact-list li { display: flex; align-items: center; height: 26.8px; }
  .contact-list svg { width: 18px; height: 18px; margin-right: 12px; flex: none; fill: var(--brand-red); }
</style>
</head>
<body>
  <section class="card card-front">
    <div class="wordmark">BrindleStaffing</div>

    <svg class="name-band" viewBox="0 0 387 97" aria-hidden="true">
      <polygon points="0,0 387,0 387,97 60,97" fill="var(--brand-yellow)"/>
      <polygon points="9,0 387,0 387,97 68,97" fill="var(--brand-red)"/>
    </svg>
    <div class="name-block">
      <div class="person-name">Gordon Pratley</div>
      <div class="person-title">Chairman</div>
    </div>

    <p class="address">417 39th Avenue South<br>SAINT PETERSBURG FL 33712</p>

    <ul class="contact-list">
      <li>
        <svg viewBox="0 0 18 18" aria-label="Mobile"><rect x="4" y="0" width="10" height="18" rx="2"/><rect x="6" y="2.5" width="6" height="11" fill="#fff"/></svg>
        813-555-4172
      </li>
      <li>
        <svg viewBox="0 0 18 18" aria-label="Fax"><rect x="4" y="1" width="10" height="6" fill="#f7a9ac"/><rect x="0" y="7" width="18" height="9" rx="2"/><rect x="4" y="12" width="10" height="3" fill="#fff"/></svg>
        813-555-8036
      </li>
      <li>
        <svg viewBox="0 0 18 18" aria-label="Email"><rect x="1" y="4" width="16" height="11"/><polyline points="1.5,4.5 9,10.5 16.5,4.5" fill="none" stroke="#fff" stroke-width="1.6"/></svg>
        gpratley@brindlestaffing.com
      </li>
      <li>
        <svg viewBox="0 0 18 18" aria-label="Website"><circle cx="9" cy="9" r="8"/><path d="M5 5 Q8 6 7 9 Q5 11 6 14 M11 3 Q10 7 13 8 Q15 10 13 13" fill="none" stroke="#fff" stroke-width="1.4"/></svg>
        www.brindlestaffing.com
      </li>
    </ul>
  </section>

  <section class="card card-back">
    <div class="wordmark">BrindleStaffing</div>
  </section>
</body>
</html>
```